Small office needs Graphic works to walls

Based on the company's logo and branding, create graphic illustrations that could be applied to the walls to enhance the interiors. The company's line of work is project management.
Their corporate brand guidelines can be downloaded from this link https://www.filequarry.net/sh/kq7mzt2wplx94bd/QRTxxLmnVe3K-p81Zh-Tkwb?dl=0
Photos of the existing space (along with a Key Plan) have been uploaded.

Target Market(s)

The target is to offer clients that are visiting the office a glimpse of the company's identity and what they do

Font styles to use
Other font styles liked:
• MinionPro-Regular and Futura

Requirements
Must have
• The graphics should relate to the corporate identiy
Nice to have
• keep it simple but effective

```html
<!DOCTYPE html>
<html lang="en">
<head>
<meta charset="utf-8">
<title>Project Management Wall Graphic</title>
<link href="https://fonts.googleapis.com/css2?family=Jost:wght@400;500&display=swap" rel="stylesheet">
<style>
  :root {
    --wall: #ffffff;
    --ink: #161616;
    --blue: #2a86c0;
    --teal: #1f5d7c;
  }
  html, body {
    margin: 0;
    width: 1200px;
    height: 600px;
    overflow: hidden;
    background: var(--wall);
  }
  .canvas {
    position: relative;
    width: 1200px;
    height: 600px;
    overflow: hidden;
    background: var(--wall);
    font-family: "Jost", "Futura", sans-serif;
    font-weight: 500;
  }
  .term-wall {
    position: absolute;
    left: 40px;
    top: 70px;
    width: 1120px;
    height: 460px;
    margin: 0;
    padding: 0;
    list-style: none;
    display: flex;
    flex-wrap: wrap;
    justify-content: center;
    align-items: baseline;
    align-content: center;
    gap: 4px 20px;
  }
  .term {
    margin: 0;
    line-height: 1.15;
    white-space: nowrap;
  }
  .term--xl { font-size: 46px; }
  .term--l  { font-size: 32px; }
  .term--m  { font-size: 24px; }
  .term--s  { font-size: 16px; font-weight: 400; }
  .ink  { color: var(--ink); }
  .blue { color: var(--blue); }
  .teal { color: var(--teal); }
</style>
</head>
<body>
<main class="canvas">
  <ul class="term-wall" aria-label="Project management services">
    <li class="term term--m ink">Client Investment Requirements</li>
    <li class="term term--s ink">Funding Structure</li>
    <li class="term term--l teal">Technology</li>
    <li class="term term--m teal">Business Continuity</li>
    <li class="term term--s ink">Scheme Design</li>

    <li class="term term--xl ink">Development Management</li>
    <li class="term term--l blue">Internal Approvals</li>
    <li class="term term--s ink">Leasing</li>

    <li class="term term--m teal">Local Authorities Aproval</li>
    <li class="term term--l blue">Quality Assurance</li>
    <li class="term term--xl teal">Facilities Management</li>

    <li class="term term--s blue">Consultant</li>
    <li class="term term--m blue">Input</li>
    <li class="term term--m blue">Program &amp; Milestone Deliveries</li>
    <li class="term term--s teal">Management Contractors</li>
    <li class="term term--m teal">Operation Costs</li>

    <li class="term term--l blue">End User Functional Needs</li>
    <li class="term term--m blue">Contractors Deliverables</li>
    <li class="term term--s teal">Design, Construction, Commission &amp; Occupancy</li>

    <li class="term term--l ink">Sales</li>
    <li class="term term--xl blue">Project Management</li>
    <li class="term term--l teal">Operational Risk</li>

    <li class="term term--s ink">Financial Partners</li>
    <li class="term term--m teal">Asset Register</li>
    <li class="term term--s ink">Construction</li>
    <li class="term term--m blue">External Approvals</li>
    <li class="term term--l teal">Life Cycle Costs</li>
    <li class="term term--s teal">Occupants</li>

    <li class="term term--l blue">Client Requirements</li>
    <li class="term term--m teal">Client Asset Performance Requirements</li>
    <li class="term term--s ink">Program &amp; Milestone Deliverables</li>

    <li class="term term--m ink">Land Use &amp; Development Mix</li>
    <li class="term term--s teal">Management Performance</li>
    <li class="term term--s blue">Funding &amp; Financial Returns</li>
    <li class="term term--m teal">Building Asset</li>
  </ul>
</main>
</body>
</html>
```